Kellwyn Surface Records

I have a current web site that it looking quite aged and it needs a new lease of life. This is a Graffiti Management Website so is all about data processing and management of information. I want a html 5 view on any platform design. clean crisp and new. I have provided some screen shots of my current site.

Target Market(s)

The Target Market will be local government. most users will not be heavy pc users

Industry/Entity Type

Management

Font styles to use
Sans Serif
Other font styles liked:
• web font like calibri

Colors

Designer to choose colors to be used in the design.

Requirements
Must have
• Must have menus similar to attachments

```html
<!DOCTYPE html>
<html lang="en">
<head>
<meta charset="utf-8">
<title>Kellwyn Surface Records</title>
<link rel="stylesheet" href="https://fonts.googleapis.com/css2?family=Open+Sans:wght@400;600&display=swap">
<style>
:root{
  --sky:#4f93d4;
  --navy:#03135e;
  --brand:#0a5cc2;
  --brand-deep:#0344b3;
  --hero-light:#1e86e0;
  --ink:#111;
  --muted:#555;
  --footer:#1a1a1a;
  --white:#fff;
}
*{margin:0;padding:0;box-sizing:border-box}
html,body{width:1200px;height:1131px;overflow:hidden}
body{font-family:"Open Sans",Arial,sans-serif;background:var(--white);position:relative;color:var(--ink)}
.masthead{position:absolute;left:0;top:0;width:1200px;height:80px;background:linear-gradient(#5a9ddb,#3f86cc)}
.masthead-band{position:absolute;left:0;top:61px;width:1200px;height:19px;background:var(--navy);border-top:2px solid #dfe9f5}
.brand{position:absolute;left:400px;top:6px;width:400px;text-align:center;color:var(--white);z-index:1}
.brand-mark{font-weight:600;font-size:40px;letter-spacing:40px;line-height:44px;padding-left:40px}
.brand-name{font-weight:600;font-size:13px;letter-spacing:2px;margin-top:14px;line-height:16px}
.main-nav{position:absolute;left:0;top:80px;width:1200px;height:50px;background:linear-gradient(#fff,#eef0f2);border-bottom:1px solid #d8dbe0}
.main-nav a{position:absolute;top:16px;font-size:14px;font-weight:600;color:var(--ink);text-decoration:none}
.hero{position:absolute;left:0;top:130px;width:1200px;height:440px;background:radial-gradient(ellipse at 40% 55%,var(--hero-light) 0%,var(--brand-deep) 55%,#0236a0 100%)}
.hero h1{position:absolute;left:51px;top:86px;width:420px;font-weight:400;font-size:27px;line-height:31px;color:var(--white)}
.hero p{position:absolute;left:51px;top:174px;width:370px;font-size:11px;line-height:16px;color:var(--white)}
.hero-button{position:absolute;left:51px;top:228px;width:92px;height:32px;background:#ececec;border-radius:2px;font-size:14px;line-height:32px;text-align:center;color:#333}
.slider-dots{position:absolute;left:52px;top:299px;width:83px;height:18px;background:#052f7e;border-radius:9px}
.slider-dots span{position:absolute;top:5px;width:8px;height:8px;border-radius:50%;background:var(--white)}
.slider-dots span.current{background:none;border:1.5px solid var(--white)}
.hero-visual{position:absolute;left:628px;top:44px;width:444px;height:352px;border-radius:8px;background:linear-gradient(180deg,#1c1c1e 0%,#3a3d42 30%,#b9bdc3 75%,#d6d9dd 100%)}
.features{position:absolute;left:0;top:570px;width:1200px}
.feature{position:absolute;top:61px;width:230px;text-align:center}
.feature svg{display:block;margin:0 auto}
.feature h2{margin-top:22px;font-size:15px;font-weight:600;line-height:21px;color:var(--brand)}
.feature p{margin:20px auto 0;width:216px;font-size:12.5px;line-height:20.5px;color:var(--muted)}
.site-footer{position:absolute;left:0;top:1004px;width:1200px;height:127px;background:var(--footer);color:var(--white)}
.footer-nav a{position:absolute;top:42px;font-size:12.5px;color:var(--white);text-decoration:none}
.copyright{position:absolute;left:51px;top:71px;font-size:11px}
.social span{position:absolute;top:58px;width:12px;height:12px;border-radius:50%;background:#cfcfcf}
</style>
</head>
<body>
<header class="masthead">
  <div class="masthead-band"></div>
  <div class="brand">
    <div class="brand-mark">KSR</div>
    <div class="brand-name">KELLWYN SURFACE RECORDS</div>
  </div>
</header>
<nav class="main-nav">
  <a href="#" style="left:52px">HOME</a>
  <a href="#" style="left:150px">PRODUCTS</a>
  <a href="#" style="left:280px">BENEFITS</a>
  <a href="#" style="left:398px">LEGISLATION</a>
  <a href="#" style="left:541px">CONTACT US</a>
</nav>
<section class="hero">
  <h1>KSR PROVIDES A NATIONAL REGISTER</h1>
  <p>Vandalism and Graffiti. Subscribers to the KSR Database can Add, Change, Report on and Archive their own Graffiti Jobs.</p>
  <div class="hero-button">Contact us</div>
  <div class="slider-dots">
    <span class="current" style="left:11px"></span>
    <span style="left:29px"></span>
    <span style="left:47px"></span>
    <span style="left:65px"></span>
  </div>
  <div class="hero-visual" role="img" aria-label="Desktop monitor showing a rising trend chart"></div>
</section>
<section class="features">
  <div class="feature" style="left:43px">
    <svg width="106" height="106" viewBox="0 0 106 106"><circle cx="53" cy="53" r="53" fill="var(--brand)"/><rect x="35" y="30" width="36" height="46" fill="none" stroke="#fff" stroke-width="4"/><rect x="45" y="25" width="16" height="9" fill="#fff"/></svg>
    <h2>GRAFFITI<br>REGISTER</h2>
    <p>KSR provides a National Register of Vandalism and Graffiti. Subscribers to the KSR Database can Add, Change, Report on and Archive their own Graffiti Jobs.</p>
  </div>
  <div class="feature" style="left:343px">
    <svg width="106" height="106" viewBox="0 0 106 106"><circle cx="53" cy="53" r="53" fill="var(--brand)"/><rect x="27" y="27" width="40" height="40" fill="#fff"/><rect x="39" y="39" width="40" height="40" fill="var(--brand)" stroke="#fff" stroke-width="5"/></svg>
    <h2>GRAFFITI<br>PHOTOS</h2>
    <p>KSR provides a National Register of Vandalism and Graffiti. Subscribers to the KSR Database can Add, Change, Report on and Archive their own Graffiti Jobs.</p>
  </div>
  <div class="feature" style="left:635px">
    <svg width="106" height="106" viewBox="0 0 106 106"><circle cx="53" cy="53" r="53" fill="var(--brand)"/><circle cx="53" cy="53" r="30" fill="none" stroke="#fff" stroke-width="5"/><path d="M30 40 L53 53 L76 45 M53 53 L48 82 M53 53 L62 26" stroke="#fff" stroke-width="5" fill="none"/><circle cx="53" cy="53" r="6" fill="#fff"/></svg>
    <h2>GRAFFITI<br>ARCHIVE</h2>
    <p>KSR provides a National Register of Vandalism and Graffiti. Subscribers to the KSR Database can Add, Change, Report on and Archive their own Graffiti Jobs.</p>
  </div>
  <div class="feature" style="left:925px">
    <svg width="106" height="106" viewBox="0 0 106 106"><circle cx="53" cy="53" r="53" fill="var(--brand)"/><rect x="30" y="28" width="38" height="48" fill="none" stroke="#fff" stroke-width="4"/><path d="M37 40h24M37 49h18M37 58h12" stroke="#fff" stroke-width="4"/><circle cx="65" cy="64" r="8" fill="var(--brand)" stroke="#fff" stroke-width="4"/><path d="M71 70l9 9" stroke="#fff" stroke-width="5"/></svg>
    <h2>SEARCHABLE<br>DATABASE</h2>
    <p>KSR provides a National Register of Vandalism and Graffiti. Subscribers to the KSR Database can Add, Change, Report on and Archive their own Graffiti Jobs.</p>
  </div>
</section>
<footer class="site-footer">
  <nav class="footer-nav">
    <a href="#" style="left:51px">HOME</a>
    <a href="#" style="left:137px">PRODUCTS</a>
    <a href="#" style="left:251px">BENEFITS</a>
    <a href="#" style="left:354px">LEGISLATION</a>
    <a href="#" style="left:479px">CONTACT US</a>
  </nav>
  <div class="copyright">Copyright © 2014. All rights reserved.</div>
  <div class="social">
    <span style="left:921px"></span>
    <span style="left:957px"></span>
    <span style="left:992px"></span>
    <span style="left:1028px"></span>
    <span style="left:1062px"></span>
    <span style="left:1097px"></span>
    <span style="left:1132px"></span>
  </div>
</footer>
</body>
</html>
```